Stylish business cards for KV7

To create an appealing and professional business card design for a WOMEN Owned Construction Supply Company.
2 sided card. Incorporate brand elements, curvy, colorful, sleek and bright. No solid white background. attached samples of styles added shapes/ribbons. Want something with that WOW that looks awesome, factor. It is a new logo, so feel free to mess with logo colors in the blue and teal factors that can look good with both dark and light background. If you want to try a watermark with just the KV7, without the "Supply" that might look cool to.

Industry/Entity Type

Women owned construction supply company

Contact Information for Business Card

Name, Title, and phone number and email, web page. maybe spot for qr code.

Font styles to use
Sans Serif

Requirements
Nice to have
• would love to see colors, maybe stylish ribbon dividers or some sort of 2 or 3 tone color card that compliments logo.
Should not have
• Please do not have all white background. Do not include Home/reale state/ or building images.

```html
<!DOCTYPE html>
<html lang="en">
<head>
<meta charset="utf-8">
<title>KV7 Supply – Business Card</title>
<link href="https://fonts.googleapis.com/css2?family=Montserrat:wght@400;600;700&display=swap" rel="stylesheet">
<style>
  :root {
    --stage: #1c1c1e;
    --card-navy: #1b3a5c;
    --navy-deep: #15304d;
    --teal: #2a9bc2;
    --white: #f4f6f8;
  }
  * { box-sizing: border-box; margin: 0; padding: 0; }
  html, body {
    width: 1200px; height: 1059px; overflow: hidden;
    background: var(--stage);
    font-family: "Montserrat", sans-serif;
  }
  .canvas { position: relative; width: 1200px; height: 1059px; }
  .card {
    position: absolute; left: 255px; width: 690px; height: 392px;
    background: var(--card-navy); border-radius: 18px; overflow: hidden;
  }
  .card--front { top: 89px; }
  .card--back { top: 546px; }

  .brand-name {
    position: absolute; font-weight: 700; color: var(--white);
    white-space: nowrap; letter-spacing: 0.5px;
  }
  .card--front .brand-name { left: 31px; top: 72px; font-size: 36px; }
  .card--back .brand-name {
    left: 0; right: 0; top: 160px; text-align: center; font-size: 64px;
  }

  .watermark {
    position: absolute; right: 22px; bottom: 20px;
    font-weight: 700; font-size: 230px; line-height: 1;
    color: var(--navy-deep); letter-spacing: -4px;
  }

  .accent-bar {
    position: absolute; left: 0; top: 190px; width: 15px; height: 35px;
    background: var(--teal);
  }
  .person { position: absolute; left: 31px; top: 189px; }
  .person__name {
    font-size: 21px; font-weight: 700; color: var(--teal);
    letter-spacing: 0.3px; line-height: 1.1;
  }
  .person__title { font-size: 14px; color: var(--white); margin-top: 3px; }
  .address {
    position: absolute; left: 31px; top: 242px;
    font-size: 14.5px; line-height: 20px; color: var(--white);
  }
  .contacts {
    position: absolute; left: 31px; top: 292px; list-style: none;
    font-size: 14.5px; color: var(--white);
  }
  .contacts li { display: flex; align-items: center; height: 25px; }
  .contacts svg { width: 12px; height: 12px; margin-right: 7px; fill: var(--teal); }
</style>
</head>
<body>
<div class="canvas">

  <section class="card card--front">
    <div class="watermark" aria-hidden="true">KV7</div>
    <div class="brand-name">KV7 Supply</div>

    <span class="accent-bar"></span>
    <div class="person">
      <p class="person__name">DANA WHITFIELD</p>
      <p class="person__title">CEO/Founder</p>
    </div>
    <p class="address">P.O Box 4127 Harbour Road<br>Lakeview QL 40210</p>
    <ul class="contacts">
      <li>
        <svg viewBox="0 0 24 24" aria-hidden="true"><path d="M6.6 10.8a15.1 15.1 0 0 0 6.6 6.6l2.2-2.2c.3-.3.7-.4 1-.2 1.1.4 2.3.6 3.6.6.6 0 1 .4 1 1V20c0 .6-.4 1-1 1C10.6 21 3 13.4 3 4c0-.6.4-1 1-1h3.5c.6 0 1 .4 1 1 0 1.3.2 2.5.6 3.6.1.3 0 .7-.2 1z"/></svg>
        555.318.2740
      </li>
      <li>
        <svg viewBox="0 0 24 24" aria-hidden="true"><path d="M2 5h20v14H2z M2 5l10 8 10-8" fill="none" stroke="#2a9bc2" stroke-width="2.4"/></svg>
        info@kv7supply.com.au
      </li>
      <li>
        <svg viewBox="0 0 24 24" aria-hidden="true"><g fill="none" stroke="#2a9bc2" stroke-width="2"><circle cx="12" cy="12" r="10"/><ellipse cx="12" cy="12" rx="4.5" ry="10"/><path d="M2 12h20M4 7h16M4 17h16"/></g></svg>
        www.kv7supply.com.au
      </li>
    </ul>
  </section>

  <section class="card card--back">
    <div class="brand-name">KV7 Supply</div>
  </section>

</div>
</body>
</html>
```